Business card design for Automotive workshop

We need a business card for a new automotive repair and tyre shop called Keelstone Prime Automotive located in New Zealand. We are a clean, modern and fresh workshop and company.

Front needs to feature logo,
my name:
Marlo Fenwicke (director)

Address:
48 Tarn Lane
Kereru Bay 3588

Phone: 07 594 2713
Mobile: 027 451 9362
Email: office@keelstoneautomotive.example.nz
Website: keelstoneautomotive.example.nz

Back needs to feature an area to write down appointment details, date and time.

Also feature a list of jobs and work we do such as,
Vehicle Servicing
All Mechanical Repairs
Warrant of Fitness
Tyres & Wheel Alignments
Automotive Diagnostics
Automotive Parts & Supplies

```html
<!DOCTYPE html>
<html lang="en">
<head>
<meta charset="utf-8">
<title>Keelstone Prime Automotive – Business Card</title>
<link href="https://fonts.googleapis.com/css2?family=Open+Sans:ital,wght@0,400;0,600;0,700;1,600&display=swap" rel="stylesheet">
<style>
  :root{
    --stage:#2b2827;
    --card:#111111;
    --panel:#333333;
    --red:#e31b23;
    --white:#ffffff;
    --silver:#9a9a9a;
    --dash:#8a8a8a;
  }
  *{box-sizing:border-box;margin:0;padding:0}
  html,body{width:1200px;height:716px;overflow:hidden;background:var(--stage)}
  body{position:relative;font-family:"Open Sans",Arial,sans-serif;color:var(--white)}
  .card{position:absolute;top:193px;width:540px;height:330px;background:var(--card);overflow:hidden;box-shadow:0 10px 30px rgba(0,0,0,.45)}
  .card--back{left:35px}
  .card--front{left:625px}

  /* back */
  .appointment{position:absolute;left:34px;top:30px;width:472px;height:160px;background:var(--panel)}
  .appointment__title{position:absolute;top:18px;width:100%;text-align:center;color:var(--red);font-weight:600;font-style:italic;font-size:20px;letter-spacing:.3px}
  .field{position:absolute;display:flex;align-items:flex-end;font-weight:700;font-size:13px}
  .field__line{flex:1;border-bottom:1px dashed var(--dash);margin-left:6px;margin-bottom:3px}
  .field--date{left:18px;top:80px;width:270px}
  .field--time{left:250px;top:118px;width:204px}
  .works{position:absolute;left:0;top:212px;width:100%;display:flex;align-items:center;justify-content:center;gap:12px;font-weight:700;font-size:13px}
  .works__rule{width:92px;height:1.5px;background:var(--red)}
  .works-list{position:absolute;left:0;top:244px;width:100%;text-align:center;font-size:11.5px;line-height:22px}
  .works-list span{white-space:nowrap;margin:0 5px}
  .works-list span::before{content:"";display:inline-block;width:5px;height:5px;border-radius:50%;background:var(--red);margin-right:5px;vertical-align:2px}

  /* front */
  .brand{position:absolute;right:40px;top:84px;width:300px;text-align:center;color:var(--silver);font-weight:700;font-size:25px;line-height:30px;letter-spacing:1px;text-transform:uppercase}
  .person{position:absolute;left:80px;top:196px;width:172px;text-align:right}
  .person__name{color:var(--red);font-weight:600;font-size:21px;white-space:nowrap}
  .person__role{font-size:12.5px;margin-top:4px}
  .divider{position:absolute;left:268px;top:190px;width:1px;height:72px;background:#9a9a9a}
  .contact{position:absolute;left:282px;top:186px;list-style:none;font-size:11.5px;line-height:19px}
  .contact li{display:flex;align-items:center;gap:7px;white-space:nowrap}
  .contact svg{width:10px;height:10px;fill:var(--red);flex:none}
  .address-band{position:absolute;left:0;bottom:22px;width:100%;height:34px;background:var(--red);display:flex;align-items:center;justify-content:center;font-size:13px}
</style>
</head>
<body>
  <section class="card card--back" aria-label="Card back">
    <div class="appointment">
      <h2 class="appointment__title">Appointment Details</h2>
      <div class="field field--date">Date<span class="field__line"></span></div>
      <div class="field field--time">Time<span class="field__line"></span></div>
    </div>
    <div class="works"><span class="works__rule"></span>Our Works<span class="works__rule"></span></div>
    <p class="works-list">
      <span>Vehicle Servicing</span><span>Warrant of Fitness</span><span>Automotive Parts &amp; Supplies</span><br>
      <span>Automotive Diagnostics</span><span>Tyres &amp; Wheel Alignments</span><span>All Mechanical Repairs</span>
    </p>
  </section>

  <section class="card card--front" aria-label="Card front">
    <p class="brand">Keelstone Prime<br>Automotive</p>
    <div class="person">
      <p class="person__name">Marlo Fenwicke</p>
      <p class="person__role">Director</p>
    </div>
    <span class="divider"></span>
    <ul class="contact">
      <li><svg viewBox="0 0 10 10"><path d="M2 0.5 L3.6 2.6 L2.8 3.6 Q4 6 6.4 7.2 L7.4 6.4 L9.5 8 L8.4 9.5 Q1 8 0.5 1.6 Z"/></svg>07 594 2713</li>
      <li><svg viewBox="0 0 10 10"><path d="M2.5 0 H7.5 V10 H2.5 Z M3.4 1 V8 H6.6 V1 Z"/></svg>027 451 9362</li>
      <li><svg viewBox="0 0 10 10"><path d="M0 1.5 H10 V8.5 H0 Z M1 2.5 L5 5.5 L9 2.5 V2.2 H1 Z"/></svg>office@keelstoneautomotive.example.nz</li>
      <li><svg viewBox="0 0 10 10"><path d="M5 0 A5 5 0 1 0 5 10 A5 5 0 1 0 5 0 Z M5 1.2 A3.8 3.8 0 1 1 5 8.8 A3.8 3.8 0 1 1 5 1.2 Z M4.4 1.2 H5.6 V8.8 H4.4 Z M1.2 4.4 H8.8 V5.6 H1.2 Z"/></svg>keelstoneautomotive.example.nz</li>
    </ul>
    <p class="address-band">48 Tarn Lane Kereru Bay 3588</p>
  </section>
</body>
</html>
```